Graphic Design Project

We make rose petal jelly from old fashioned english roses. The jelly is sweet eaten with scones and clotted cream or as a filling in a victoria sandwich, as a topping on ice cream or thick set yogurt.
The image of the product is luxurious and decadent and very english.
We need a design for a label which has a picture of an old fashioned rose (rosa mundi or a compte de chambard) The rose must stand out clearly so the jelly is not confused with other fruit jams. The overall colour of the label should be pink and soft, with white or dark pink writing. The label needs to be fridge proof.

We also need a security strip to fit on the lid of the jar.

We need the following information on the label.
Name of our company-"Meadow Crown"
Name of Product-"Rose Petal Jelly"
Sales pitch-"With whole petals-a taste of summer, delicious on scones, as a filling in sponge cake, as a topping on ice cream or yogurt."
INGREDIENTS: Sugar, water, rose petals, lemon juice, natural jelling agent (agar-agar)
STORAGE: Store in a cool dry place, once opened keep refrigerated and consume within 4 weeks.
BEST BEFORE: See base

200g
Produced by:
MEADOW CROWN
The Larches
Pardew Lane
Brockwell
Thornshire
GL17 4RX
The label must have room for a bar code. The size of label approx 8-10cm long 5cm wide.
Updates

Hi

Just been looking at the Hartwell and Brace site and the labels they have there have the up market feel I am trying to convey. Hope that helps, its classy but not twee.

Thanks

Thanks for all submissions. I would be grateful if you googled images for 'Colourful and expensive biscuits at Hartwell Brace' The designs on the tins are the image we are trying to create. The colours are quite strong.

Thanks

Target Market(s)

older well off people who visit garden centres

Industry/Entity Type

Security

Requirements
Must have
• All writen info above and picture of old fashioned rose prferably rose a mundi. Luxury feel, very english, to appeal to older market
Pink colour sheme
Should not have
• dark or manly colours

```html
<!DOCTYPE html>
<html lang="en">
<head>
<meta charset="utf-8">
<title>Meadow Crown – Rose Petal Jelly Label</title>
<link rel="stylesheet" href="https://fonts.googleapis.com/css2?family=Pinyon+Script&family=Quicksand:wght@500;600&display=swap">
<style>
  :root {
    --paper-light: #f3d9c2;
    --paper-mid: #ebc0a8;
    --paper-edge: #dea48f;
    --ink-dark: #8e1b2c;
    --ink-red: #b1243c;
    --ink-pink: #c63d62;
    --rose-cream: #efd2a6;
    --rose-gold: #d9a56a;
    --rose-pink: #d98aa0;
  }
  * { margin: 0; padding: 0; box-sizing: border-box; }
  html, body { width: 1200px; height: 600px; overflow: hidden; background: #ffffff; }
  .label {
    position: relative;
    width: 1200px;
    height: 600px;
    overflow: hidden;
    background:
      radial-gradient(ellipse 55% 60% at 60% 45%, rgba(250, 232, 210, 0.75), rgba(250, 232, 210, 0) 70%),
      radial-gradient(ellipse 40% 50% at 15% 80%, rgba(214, 140, 130, 0.35), rgba(214, 140, 130, 0) 70%),
      linear-gradient(135deg, var(--paper-mid) 0%, var(--paper-light) 45%, var(--paper-mid) 75%, var(--paper-edge) 100%);
    font-family: "Quicksand", "Trebuchet MS", sans-serif;
  }
  .producer-info {
    position: absolute;
    left: 30px;
    top: 24px;
    width: 440px;
    color: var(--ink-red);
    font-size: 16px;
    font-weight: 500;
    line-height: 26px;
  }
  .producer-info p + p { margin-top: 26px; }
  .brand-name {
    position: absolute;
    left: 500px;
    top: 18px;
    width: 600px;
    text-align: center;
    font-family: "Pinyon Script", cursive;
    font-size: 92px;
    font-weight: 400;
    line-height: 1.1;
    color: var(--ink-dark);
    text-shadow: 2px 2px 3px rgba(255, 240, 230, 0.7);
  }
  .product-name {
    position: absolute;
    left: 500px;
    top: 124px;
    width: 600px;
    text-align: center;
    font-family: "Pinyon Script", cursive;
    font-size: 54px;
    font-weight: 400;
    line-height: 1.1;
    color: var(--ink-pink);
    text-shadow: 1px 1px 2px rgba(255, 240, 230, 0.7);
  }
  .sales-pitch {
    position: absolute;
    left: 470px;
    top: 206px;
    width: 670px;
    text-align: center;
    color: var(--ink-dark);
    font-size: 20px;
    font-weight: 500;
    line-height: 28px;
  }
  .rose-illustration {
    position: absolute;
    left: 665px;
    top: 283px;
    width: 270px;
    height: 267px;
  }
  .net-weight {
    position: absolute;
    left: 760px;
    top: 566px;
    width: 115px;
    text-align: center;
    color: var(--ink-dark);
    font-size: 18px;
    font-weight: 500;
  }
</style>
</head>
<body>
  <div class="label">
    <div class="producer-info">
      <p>Produced by:<br>MEADOW CROWN<br>The Larches<br>Pardew Lane<br>Brockwell<br>Thornshire<br>GL17 4RX</p>
      <p>INGREDIENTS: Sugar, water, rose petals,<br>lemon juice, natural jelling agent (agar-agar)</p>
      <p>STORAGE: Store in a cool dry place, once opened<br>keep refrigerated and consume within 4 weeks.</p>
      <p>BEST BEFORE: See base</p>
    </div>

    <h1 class="brand-name">Meadow Crown</h1>
    <h2 class="product-name">Rose Petal Jelly</h2>

    <p class="sales-pitch">With whole petals-a taste of summer, delicious on scones,<br>as a filling in sponge cake, as a topping on ice cream or yogurt.</p>

    <svg class="rose-illustration" viewBox="0 0 270 267" role="img" aria-label="Painted illustration of an old fashioned English rose in cream, gold and soft pink">
      <defs>
        <radialGradient id="roseFill" cx="50%" cy="50%" r="50%">
          <stop offset="0%" stop-color="#d9a56a"/>
          <stop offset="45%" stop-color="#efd2a6"/>
          <stop offset="80%" stop-color="#d98aa0"/>
          <stop offset="100%" stop-color="#d98aa0" stop-opacity="0"/>
        </radialGradient>
      </defs>
      <ellipse cx="135" cy="133" rx="135" ry="133" fill="url(#roseFill)"/>
    </svg>

    <div class="net-weight">200 g</div>
  </div>
</body>
</html>
```